BUSINESS CARD - HALLORAN FIELD SERVICES

I would like to create a business card for my fertilizer spreading business. I would like to incorporate my existing logo and also a description of the services offered. The business card will be given to farmers so must be kept simple but effective. It will also be left in stores so much also be eye catching in order to stand out from other cards.

Target Market(s)

FARMERS

Requirements
Must have
• FRONT OF CARD = EXISTING LOGO + "CUSTOMISED SPREADING" below the logo

REAR Of CARD = SERVICES OFFERED AND CONTACT DETAILS

- Bulk fertilizer including Lime, Gypsum, Manure & Compost
- Granular fertilizer including Single Super, Urea, Gran-am, & Custom Blends
- Modern equipment - Autosteer & Variable Rate Capable
- Friendly & Reliable Service
- Contact Gus: 0417 552 308
Nice to have
• utilize same color scheme as existing logo

```html
<!DOCTYPE html>
<html lang="en">
<head>
<meta charset="utf-8">
<title>Halloran Field Services – Business Card</title>
<link rel="stylesheet" href="https://fonts.googleapis.com/css2?family=Arimo:wght@400;700&family=Exo+2:wght@700&display=swap">
<style>
  :root {
    --backdrop: #dcdcdc;
    --orange: #f39322;
    --paper: #f7f7f7;
    --ink: #4a4a4c;
    --white: #ffffff;
  }
  * { box-sizing: border-box; margin: 0; padding: 0; }
  html, body {
    width: 1200px;
    height: 930px;
    overflow: hidden;
    background: var(--backdrop);
  }
  .sheet {
    width: 1200px;
    height: 930px;
    display: flex;
    flex-direction: column;
    align-items: center;
    justify-content: center;
    gap: 50px;
  }
  .card {
    width: 700px;
    height: 400px;
    box-shadow: 0 4px 14px rgba(0, 0, 0, 0.12);
    display: flex;
    flex-direction: column;
    align-items: center;
    justify-content: center;
  }

  /* Front */
  .card--front { background: var(--orange); color: var(--white); }
  .brand {
    display: flex;
    align-items: center;
    gap: 22px;
  }
  .brand__mark {
    width: 110px;
    height: 110px;
    border-radius: 50%;
    background: var(--white);
    flex: none;
  }
  .brand__name {
    font-family: "Exo 2", sans-serif;
    font-weight: 700;
    font-size: 46px;
    line-height: 1.02;
    letter-spacing: -0.5px;
    color: var(--white);
  }
  .tagline {
    margin-top: 26px;
    font-family: "Exo 2", sans-serif;
    font-weight: 700;
    font-size: 30px;
    letter-spacing: 2px;
    text-transform: uppercase;
  }

  /* Back */
  .card--back { background: var(--paper); color: var(--ink); }
  .wordmark {
    font-family: "Exo 2", sans-serif;
    font-weight: 700;
    font-size: 44px;
    letter-spacing: -0.5px;
    color: var(--ink);
    margin-bottom: 22px;
  }
  .services {
    list-style: none;
    text-align: center;
    font-family: Arimo, sans-serif;
    font-size: 17px;
    line-height: 1.45;
  }
  .contact {
    margin-top: 18px;
    font-family: Arimo, sans-serif;
    font-size: 26px;
  }
  .contact__phone { color: var(--orange); }
</style>
</head>
<body>
<main class="sheet">
  <section class="card card--front" aria-label="Card front">
    <div class="brand">
      <span class="brand__mark" aria-hidden="true"></span>
      <span class="brand__name">Halloran<br>Field Services</span>
    </div>
    <p class="tagline">Customised Spreading</p>
  </section>

  <section class="card card--back" aria-label="Card back">
    <p class="wordmark">Halloran Field Services</p>
    <ul class="services">
      <li>Bulk fertilizer including Lime, Gypsum, Manure &amp; Compost</li>
      <li>Granular fertilizer including Single Super, Urea</li>
      <li>Gran-am, &amp; Custom Blends</li>
      <li>Modern equipment</li>
      <li>Autosteer &amp; Variable Rate Capable</li>
      <li>Friendly &amp; Reliable Service</li>
    </ul>
    <p class="contact">Contact Gus: <span class="contact__phone">0417 552 308</span></p>
  </section>
</main>
</body>
</html>
```